Lotus Ridge Website

We need a website that has clean, asian looking images that relax and motivate people to come into our integrated medical center. My current website is www.needlecalmharbor.com and I would like the design for Lotus Ridge Wellness Partners to be similar but more inviting with video content and a product purchase store as well. A moving banner would be nice too. When people are looking for ways of losing weight or getting out of pain we want them to make the connection that we have the solution. This website needs to provide sufficient information so that patients are well informed and choose us as their health provider before they ever walk through our doors. We offer comprehensive natural medicine that is based on the principles that the body can heal itself when given the right conditions. Our services include medical weight loss and hormone balancing, acupuncture and chinese herbal medicine, physical medicine, trigger point injections, allergy testing and joint rehabilitation. The Medical Doctor and Licensed Acupuncturist work as a team to provide optimal care that is catered to each individual who comes through our doors.
Updates

Target Market(s)

40 to 50 year olds who want to lose weight or have pain issues.

Industry/Entity Type

Medical

Requirements
Must have
• Use photos from our website www.needlecalmharbor.com or similar content. Video content. Moving banner with relaxing images.
Nice to have
• Happy, healthy looking people. Medical Doctors working as a team. Friendly staff in a cutting edge facility.
Should not have
• Papyrus font, or big bold words.

```html
<!DOCTYPE html>
<html lang="en">
<head>
<meta charset="utf-8">
<title>Lotus Ridge Acupuncture</title>
<link href="https://fonts.googleapis.com/css2?family=Source+Sans+3:wght@400;600;700&family=Arimo:wght@400&display=swap" rel="stylesheet">
<style>
:root{
  --green-dark:#5f7f22;
  --green-mid:#9bb43a;
  --lime:#d9df6a;
  --cream:#f2f0dc;
  --beige:#e4e1c6;
  --beige-dark:#cfcaa4;
  --panel:#efecdb;
  --panel-border:#d9d4b8;
  --purple:#8d4f83;
  --purple-dark:#763c6c;
  --plum:#7e3f6f;
  --navy:#27345a;
  --text:#555246;
  --heading:#4a4638;
  --link:#d0232a;
  --white:#ffffff;
}
*{box-sizing:border-box;margin:0;padding:0}
html,body{width:848px;height:1200px;overflow:hidden}
body{position:relative;font-family:"Arimo",Arial,sans-serif;color:var(--text);
  background:linear-gradient(180deg,var(--green-dark) 0,var(--green-mid) 120px,var(--lime) 230px,#eeeccc 330px,var(--beige) 448px,var(--beige) 1200px)}
.abs{position:absolute}
.page-bg{left:0;top:448px;width:848px;height:677px;background:linear-gradient(90deg,#ebe8d2 0,#e6e3ca 100%)}
.sidebar-bg{left:0;top:448px;width:270px;height:677px;background:linear-gradient(90deg,#d6d2ae,#cbc59e);box-shadow:2px 0 6px rgba(0,0,0,.15)}
.header-card{left:33px;top:14px;width:782px;height:434px;border-radius:10px 10px 0 0;
  background:linear-gradient(180deg,#f6f5e6 0,#c9d46a 100px,#d6dc7a 135px)}
.logo{left:48px;top:18px;width:91px;height:124px;background:var(--white);border:2px solid #6f6a3a;
  display:flex;flex-direction:column;align-items:center;justify-content:center;gap:6px}
.logo-mark{width:34px;height:34px;background:#6f6a3a;border-radius:50%}
.logo-name{font-family:"Source Sans 3",sans-serif;font-weight:600;font-size:15px;color:#6f6a3a;text-align:center;line-height:1.05}
.top-links{right:41px;top:22px;font-family:"Source Sans 3",sans-serif;font-weight:600;font-size:11.5px;color:#3c3a30;letter-spacing:.2px}
.main-nav{left:168px;top:60px;width:638px;height:42px;border-radius:6px;display:flex;overflow:hidden;
  background:linear-gradient(180deg,#fbfbf6,#dedcce);box-shadow:0 2px 4px rgba(0,0,0,.25)}
.main-nav a{flex:none;display:flex;align-items:center;justify-content:center;font-family:"Source Sans 3",sans-serif;
  font-weight:600;font-size:12.5px;color:#8a8a7a;text-decoration:none;border-right:1px solid #cfcdbc;letter-spacing:.3px}
.main-nav a:last-child{border-right:none}
.main-nav a.active{background:linear-gradient(180deg,#9d5c92,var(--purple-dark));color:var(--white)}
.dropdown{left:348px;top:105px;width:182px;background:#ebe9d8;border:1px solid #cfcbb2;box-shadow:0 2px 4px rgba(0,0,0,.15)}
.dropdown li{list-style:none;height:18.6px;padding-left:12px;font-size:11.2px;line-height:18.6px;color:#4d4a3e;border-bottom:1px solid #d5d1ba}
.cart{right:36px;top:121px;font-family:"Source Sans 3",sans-serif;font-weight:700;font-size:11.5px;color:#2c2a20;display:flex;align-items:center;gap:6px}
.cart .count{color:var(--white)}
.cart .count b{color:#f6e57a}
.banner-left{left:35px;top:147px;width:492px;height:298px;background:linear-gradient(135deg,#f7f5f1 0,#e8d2c0 45%,#d8b79c 70%,#b9b6b3 100%)}
.banner-right{left:527px;top:147px;width:286px;height:298px;background:linear-gradient(160deg,#f3f2ef 0,#e7c2a2 45%,#d33955 70%,#eae6e0 100%)}
.quote{left:36px;top:315px;width:379px;height:107px;background:rgba(60,60,60,.82);padding:9px 16px 0 54px;
  font-family:"Source Sans 3",sans-serif;font-weight:600;font-size:14.6px;line-height:19px;color:var(--white);text-align:justify}
.quote cite{display:block;text-align:right;font-style:normal;color:#f2d629;margin-top:-1px}
.slider-bar{left:58px;top:448px;width:732px;height:24px;background:linear-gradient(180deg,#e7e4d0,#dcd8bf);border-radius:0 0 6px 6px;
  box-shadow:0 2px 4px rgba(0,0,0,.2);display:flex;justify-content:center;align-items:center;gap:6px}
.slider-bar span{width:11px;height:11px;border-radius:50%;background:var(--plum)}
.side-title{font-family:"Source Sans 3",sans-serif;font-size:19.5px;color:#2f2d25;font-weight:400}
.news{left:34px;width:210px;display:flex;gap:14px}
.date{width:35px;height:37px;background:var(--navy);color:var(--white);text-align:center;border-radius:2px;flex:none}
.date b{display:block;font-family:"Source Sans 3",sans-serif;font-weight:700;font-style:italic;font-size:19px;line-height:20px}
.date small{font-size:10.5px;line-height:13px;display:block;background:#3a4a76}
.news p{font-size:11.2px;line-height:17px;color:#555246}
.news a,.more{color:var(--link);text-decoration:underline;float:right}
.video{left:34px;top:751px;width:205px;height:137px;border:3px solid var(--white);box-shadow:0 2px 5px rgba(0,0,0,.3);
  background:linear-gradient(135deg,#8d7b76,#c94d8d 50%,#d9c6c2)}
.video-bar{left:37px;top:873px;width:199px;height:12px;background:#222}
.video-bar i{position:absolute;left:0;top:4px;width:60px;height:3px;background:#c22}
.email{left:33px;top:948px;width:201px;height:32px;border:1px solid #a8a69a;border-radius:5px;background:linear-gradient(180deg,#fff,#e7e6e0);
  font-size:11.5px;font-style:italic;color:#6a6a6a;padding:9px 10px}
.btn{background:var(--purple);color:var(--white);font-family:"Source Sans 3",sans-serif;font-weight:600;font-size:15px;text-align:center;line-height:26px}
.social{left:34px;top:1081px;display:flex;gap:8px}
.social span{width:25px;height:25px;border-radius:3px}
.panel{background:var(--panel);border:1px solid var(--panel-border);border-radius:6px;box-shadow:0 1px 3px rgba(0,0,0,.08)}
.panel h2{font-family:"Source Sans 3",sans-serif;font-weight:400;font-size:19.5px;color:var(--heading)}
.panel p{font-size:11px;line-height:16.6px;text-align:justify;color:#5a5648}
.thumb{position:absolute}
.testi{position:absolute;left:14px;display:flex;gap:10px;width:290px}
.avatar{width:60px;height:54px;border:2px solid var(--white);border-radius:6px;box-shadow:0 1px 3px rgba(0,0,0,.35);flex:none;
  background:linear-gradient(160deg,#ece9e2,#d5b39a)}
.testi p{text-align:left}
.footer{left:0;top:1125px;width:848px;height:75px;background:var(--purple)}
.footer-side{left:0;top:1125px;width:270px;height:75px;background:var(--purple-dark)}
.copy{left:34px;top:1150px;font-size:10px;line-height:13px;color:#f1e7ee}
.foot-links{right:34px;top:1156px;font-size:10.5px;color:#f4eaf1}
</style>
</head>
<body>
<div class="abs page-bg"></div>
<div class="abs sidebar-bg"></div>

<header>
  <div class="abs header-card"></div>
  <div class="abs logo"><span class="logo-mark"></span><span class="logo-name">Lotus<br>Ridge</span></div>
  <nav class="abs top-links">HOME &nbsp;/&nbsp; CONTACT US &nbsp;/&nbsp; SITE MAP &nbsp;/&nbsp; SIGN IN &nbsp;/&nbsp; REGISTER</nav>
  <nav class="abs main-nav">
    <a class="active" style="width:81px">SO TAI HO</a>
    <a style="width:88px">SEITAI SHINPO</a>
    <a style="width:76px">SERVICES</a>
    <a style="width:106px">ACUPUNCTURE</a>
    <a style="width:91px">BIOGRAPHY</a>
    <a style="width:88px">NUTRITION</a>
    <a style="width:108px">MY JOURNEY</a>
  </nav>
  <div class="abs cart">Shopping Cart
    <svg width="22" height="18" viewBox="0 0 22 18"><path d="M1 3h4l3 10h10l3-8H7" fill="none" stroke="#fff" stroke-width="2"/><circle cx="9" cy="16" r="1.6" fill="#fff"/><circle cx="17" cy="16" r="1.6" fill="#fff"/></svg>
    <span class="count">( <b>Item 0</b> )</span>
  </div>
</header>

<section>
  <div class="abs banner-left" role="img" aria-label="Acupuncturist placing needles on a relaxed patient's forehead"></div>
  <div class="abs banner-right" role="img" aria-label="Smiling woman measuring her waist with a tape measure"></div>
  <blockquote class="abs quote">“The doctor of the future will give no medicine but will interest patients in the care of the human frame &nbsp;in diet and in the cause and [revention of disease”
    <cite>Harold Wendt</cite></blockquote>
  <div class="abs slider-bar"><span></span><span></span><span></span></div>
</section>

<ul class="abs dropdown">
  <li>Medical Weight Loss</li><li>Hormone Balancing</li><li>Acupuncture</li><li>Chinese Herbal Medicine</li>
  <li>Physical Medicine</li><li>Trigger Point Injections</li><li>Allergy Testing</li><li>Joint Rehabilitation</li>
</ul>

<aside>
  <h3 class="abs side-title" style="left:34px;top:498px">Latest News</h3>
  <div class="abs news" style="top:530px"><div class="date"><b>20</b><small>Feb</small></div><p>Phasellus porta. Fusce suscipit varius mi. Cum sociis natoque penibus et... <a>Read More</a></p></div>
  <div class="abs news" style="top:589px"><div class="date"><b>19</b><small>Feb</small></div><p>Phasellus porta. Fusce suscipit varius mi. Cum sociis natoque penibus et... <a>Read More</a></p></div>
  <div class="abs news" style="top:651px"><div class="date"><b>15</b><small>Feb</small></div><p>Phasellus porta. Fusce suscipit varius mi. Cum sociis natoque penibus et... <a>Read More</a></p></div>

  <h3 class="abs side-title" style="left:34px;top:721px">Watch Our Services</h3>
  <div class="abs video" role="img" aria-label="Video of a therapist treating a patient on a table"></div>
  <div class="abs video-bar"><i></i></div>

  <h3 class="abs side-title" style="left:34px;top:915px">Newsletter SignUp</h3>
  <div class="abs email">Enter Email Address</div>
  <div class="abs btn" style="left:150px;top:992px;width:83px;height:27px">Subscribe</div>

  <h3 class="abs side-title" style="left:34px;top:1050px">We are also on:</h3>
  <div class="abs social">
    <span style="background:#3b5a9a"></span><span style="background:#4fb3dd"></span><span style="background:#f08a23"></span><span style="background:#c62d22"></span>
  </div>
</aside>

<main>
  <article class="abs panel" style="left:300px;top:491px;width:514px;height:157px">
    <div class="thumb" role="img" aria-label="Traditional chart of acupuncture points on a human figure" style="left:9px;top:10px;width:135px;height:135px;background:linear-gradient(135deg,#e6c590,#c9905c)"></div>
    <h2 class="abs" style="left:155px;top:6px">How Does Acupuncture Work ?</h2>
    <p class="abs" style="left:157px;top:32px;width:342px">As the needles are carefully inserted into acupuncture points, specific cells stimulate nerve pathways that trigger a healing response to a particular organ system or area of the body. Acupuncture also acts on the autonomic nervous system and causes the release of endorphins, enkephalins and other natural pain relieving chemicals. &nbsp;At Lotus Ridge Acupuncture the system of acupuncture used is called Seitai Shinpo (which translates into</p>
  </article>

  <article class="abs panel" style="left:300px;top:662px;width:315px;height:207px">
    <h2 class="abs" style="left:14px;top:9px">Clients Testimonials</h2>
    <div class="testi" style="top:46px"><div class="avatar" role="img" aria-label="Portrait of a smiling client"></div><p>Phasellus porta. Fusce suscipit varius mi. Cum sociis natoque penibus et...<br><a class="more" style="float:none">Read More</a></p></div>
    <div class="testi" style="top:122px"><div class="avatar" role="img" aria-label="Portrait of a smiling client"></div><p>Phasellus porta. Fusce suscipit varius mi. Cum sociis natoque penibus et...<br><a class="more" style="float:none">Read More</a></p></div>
  </article>

  <article class="abs panel" style="left:632px;top:662px;width:182px;height:207px">
    <h2 class="abs" style="left:11px;top:9px">Our Products</h2>
    <div class="abs" role="img" aria-label="Boxes of acupuncture needles" style="left:15px;top:40px;width:153px;height:105px;border:1px solid #999;background:linear-gradient(135deg,#fbfbfb,#9fd0e0 50%,#f4f4f4)"></div>
    <div class="abs btn" style="left:50px;top:161px;width:83px;height:27px">View All</div>
  </article>

  <article class="abs panel" style="left:300px;top:884px;width:514px;height:196px">
    <h2 class="abs" style="left:15px;top:7px">Do the needles hurt? &nbsp;How safe is acupuncture?</h2>
    <div class="thumb" role="img" aria-label="Close-up of fine needles being placed in skin" style="left:9px;top:35px;width:135px;height:134px;background:linear-gradient(135deg,#2a2420,#a6705a 55%,#d9a98e)"></div>
    <p class="abs" style="left:157px;top:32px;width:342px">&nbsp;Acupuncture needles are engineered so precisely that usually a very mild sensation is felt, if any at all. &nbsp;The needles are about the diameter of a hair. &nbsp;Most patients report feeling deeply relaxed and often have instant pain relief.</p>
    <p class="abs" style="left:157px;top:101px;width:342px">There are very few adverse reactions to acupuncture but in some cases your condition may temporarily exacerbated following the treatment. &nbsp;This is a sign of detoxification and is considered to be a good thing. &nbsp;Soaking your feet in Epsom salts and hot water and getting in plenty of fluids and nutrition will ease the process.</p>
  </article>
</main>

<footer>
  <div class="abs footer"></div>
  <div class="abs footer-side"></div>
  <p class="abs copy">Copyright 2012 © Lotus Ridge Acupuncture<br>All Rights Reserved</p>
  <nav class="abs foot-links">So Tai Ho / Seitai Shinpo / Services &nbsp;/ &nbsp;Acupuncture / Biography / Nutrition / &nbsp;My Journey &nbsp;/ Contact Us</nav>
</footer>
</body>
</html>
```